RW Holloway LLC Business Card - Civil Engineering & Consulting Firm

We need a Business Card that is elegant, and masculine.  It is our Professional Civil Engineering & Consulting Company located in San Antonio TX (Not s construction or builder firm- no gears & no tool images please). We provide civil engineering services including  commercial site plans, grading and drainage plans, utility plans, hydraulics and hydrology, land planning, utility coordination, and other general civil engineering services related to commercial and residential development.
We have 2 existing Logos. We would like to convey reliability, strength, trustworthiness and attention to detail.  Blues and orange tones as per logo We are OK with the use of a darker blue in the mix.  We have 2 logo versions - Full Company Name Logo to go on the back of card, & Small Icon Logo for the front w/ personal Info.

Target Market(s)
Architects, Real Estate Developers, Other Strctural Engineers, Surveyers, General Contractors
Industry/Entity Type
Professional Civil Engineering
Contact Information for Business Card
Name, Position, Address, Cell & Office #, email, and company website
Font styles to use
Other font styles liked:
- Avian
Requirements
Should not have
- No Tools, No Gears, no Cranes, or Construction Equipment.

```html
<!DOCTYPE html>
<html lang="en">
<head>
<meta charset="utf-8">
<title>RW Holloway LLC – Business Card</title>
<link rel="stylesheet" href="https://fonts.googleapis.com/css2?family=Montserrat:wght@300;500;600&family=Lato:wght@400&display=swap">
<style>
  :root {
    --backdrop: #2b2b2b;
    --card-blue: #79abd6;
    --paper-white: #ffffff;
    --accent-orange: #ef8f26;
    --text-white: #ffffff;
    --card-w: 600px;
    --card-h: 343px;
  }
  * { box-sizing: border-box; margin: 0; padding: 0; }
  html, body { width: 1200px; height: 1015px; overflow: hidden; }
  body {
    background: var(--backdrop);
    display: flex;
    flex-direction: column;
    align-items: center;
    justify-content: center;
    gap: 44px;
  }
  .card {
    position: relative;
    width: var(--card-w);
    height: var(--card-h);
    background: var(--card-blue);
    overflow: hidden;
    box-shadow: 0 10px 24px rgba(0,0,0,0.45);
  }

  /* Back side: company name */
  .card--back {
    display: flex;
    align-items: center;
    justify-content: center;
  }
  .brand {
    display: flex;
    align-items: center;
    gap: 16px;
  }
  .brand__mark {
    width: 18px;
    height: 18px;
    background: var(--text-white);
  }
  .brand__name {
    font-family: "Montserrat", sans-serif;
    font-weight: 300;
    font-size: 40px;
    letter-spacing: 3px;
    color: var(--text-white);
    text-transform: uppercase;
  }

  /* Front side: personal info */
  .card__shape {
    position: absolute;
    inset: 0;
    width: 100%;
    height: 100%;
  }
  .front-brand {
    position: absolute;
    left: 345px;
    top: 100px;
    width: 230px;
    text-align: center;
    font-family: "Montserrat", sans-serif;
    font-weight: 500;
    font-size: 22px;
    letter-spacing: 1px;
    color: var(--card-blue);
    text-transform: uppercase;
    line-height: 1.3;
  }
  .person {
    position: absolute;
    left: 36px;
    top: 92px;
    color: var(--text-white);
    font-family: "Montserrat", sans-serif;
  }
  .person__name {
    font-weight: 600;
    font-size: 21px;
    letter-spacing: 0.4px;
    text-transform: uppercase;
    white-space: nowrap;
  }
  .person__title {
    font-weight: 500;
    font-size: 12px;
    letter-spacing: 0.8px;
    text-transform: uppercase;
    margin-top: 2px;
  }
  .contact {
    position: absolute;
    left: 36px;
    bottom: 30px;
    color: var(--text-white);
    font-family: "Lato", sans-serif;
    font-size: 15px;
    line-height: 1.35;
  }
  .contact__address { margin-bottom: 14px; }
  .contact__list { list-style: none; }
  .contact__item {
    display: flex;
    align-items: center;
    gap: 10px;
  }
  .contact__icon { width: 15px; height: 15px; flex: none; }
</style>
</head>
<body>

  <section class="card card--back" aria-label="Business card back">
    <div class="brand">
      <span class="brand__mark" aria-hidden="true"></span>
      <span class="brand__name">RW Holloway LLC</span>
    </div>
  </section>

  <section class="card card--front" aria-label="Business card front">
    <svg class="card__shape" viewBox="0 0 600 343" aria-hidden="true">
      <rect x="450" y="0" width="150" height="200" fill="var(--paper-white)"/>
      <circle cx="450" cy="120" r="185" fill="var(--paper-white)"/>
      <path d="M287.4 60.8 A173 173 0 0 0 434.9 292.3" fill="none" stroke="var(--accent-orange)" stroke-width="3.5"/>
    </svg>

    <div class="front-brand">RW Holloway LLC</div>

    <div class="person">
      <h1 class="person__name">Daniel Mercer</h1>
      <p class="person__title">Managing Director</p>
    </div>

    <div class="contact">
      <p class="contact__address">2180 Alamo Ridge Drive<br>San Antonio, TX 78216</p>
      <ul class="contact__list">
        <li class="contact__item">
          <svg class="contact__icon" viewBox="0 0 16 16" aria-hidden="true"><path d="M3.5 1.5l2.5 0 1 3.5-1.8 1.2a8 8 0 0 0 4.6 4.6L11 9l3.5 1v2.5c0 1-1 2-2 2C6.5 14.5 1.5 9.5 1.5 3.5c0-1 1-2 2-2z" fill="var(--text-white)"/></svg>
          <span>210-555 0147</span>
        </li>
        <li class="contact__item">
          <svg class="contact__icon" viewBox="0 0 16 16" aria-hidden="true"><rect x="1" y="3.5" width="14" height="9" fill="none" stroke="var(--text-white)" stroke-width="1.5"/><path d="M1 3.5l7 5.5 7-5.5" fill="none" stroke="var(--text-white)" stroke-width="1.5"/></svg>
          <span>info@hollowayeng.com</span>
        </li>
        <li class="contact__item">
          <svg class="contact__icon" viewBox="0 0 16 16" aria-hidden="true"><g fill="none" stroke="var(--text-white)" stroke-width="1.3"><circle cx="8" cy="8" r="6.5"/><ellipse cx="8" cy="8" rx="3" ry="6.5"/><path d="M1.5 8h13M2.5 4.8h11M2.5 11.2h11"/></g></svg>
          <span>www.hollowayeng.com</span>
        </li>
      </ul>
    </div>
  </section>

</body>
</html>
```